Website Development for vaultmerrow.com.au

Build a new Wordpress/Responsive website for vaultmerrow.com.au

Target Market(s)

Compliance Managers, Risk Managers, Information Security and Cyber Security Professionals, Chief Data/Digital Officers, Chief Operating/Financial Officers, Business Continuity Professionals, Disaster Recovery Planners, Small Business Owners, Local/Federal Government entities

Industry/Entity Type

Data Service

Coding

Coded - Design and coding required

Number of Pages Required

5+ page

Font styles to use
Sans Serif

Colors

Designer to choose colors to be used in the design.

Requirements
Must have
• 1. Site Structure: Home Page plus the following chapter-pages for a) Services b) About c) Resources d) Blog e) Contact Us
• 2. Prefer site to built on wordpress and we can purchase a theme if needed (we currently use Kelp9 for other sites)
• 3. Blog needs to be wordpress based
• 4. We will host the site ourselves on our own servers
• 5. Responsive Design
Nice to have
• 1. Livechat capability/interface
• 2. Capability for marketing automation integration (such as hubspot, marketo, infusionsoft etc)
• 3. Capability for CRM integration (Salesforce)

```html
<!DOCTYPE html>
<html lang="en">
<head>
<meta charset="utf-8">
<title>Vaultmerrow — Data Services</title>
<link href="https://fonts.googleapis.com/css2?family=Montserrat:wght@400;500;600;700&family=Open+Sans:wght@400;600&family=Roboto+Condensed:wght@400;700&display=swap" rel="stylesheet">
<style>
:root{
  --red:#e3151c;
  --red-dark:#a3070c;
  --ink:#222;
  --text:#555;
  --muted:#888;
  --grey-bg:#efefef;
  --line:#ddd;
  --white:#fff;
}
*{box-sizing:border-box;margin:0;padding:0}
html,body{width:1200px;height:3557px;overflow:hidden}
body{font-family:"Open Sans",sans-serif;color:var(--text);background:var(--white);position:relative}
a{color:inherit;text-decoration:none}
.section-title{font-family:"Montserrat",sans-serif;font-size:29px;font-weight:400;letter-spacing:2px;text-align:center;color:var(--ink)}
.section-title b{color:var(--red);font-weight:700}
.title-rule{width:60px;height:2px;background:var(--line);margin:14px auto 0}

/* header */
.site-header{position:absolute;top:0;left:0;width:1200px;height:100px;background:var(--white);display:flex;align-items:center;justify-content:space-between;padding:0 140px;z-index:2}
.brand{display:flex;align-items:center;gap:10px;font-family:"Montserrat",sans-serif;font-weight:700;font-size:32px;color:var(--red)}
.brand-mark{width:34px;height:34px;border-radius:50%;background:var(--red)}
.main-nav{display:flex;gap:34px;font-family:"Montserrat",sans-serif;font-size:14px;font-weight:500;color:#333}
.main-nav .active{color:var(--red)}

/* hero */
.hero{position:absolute;top:100px;left:0;width:1200px;height:550px;overflow:hidden}
.hero-photo{position:absolute;inset:0;background:radial-gradient(circle at 72% 42%,#e0262b 0,#8d0b10 28%,#3d0507 60%,#1c0203 100%)}
.hero-curve{position:absolute;left:0;bottom:0;width:1200px;height:120px}
.hero-copy{position:absolute;left:145px;top:120px;color:var(--white)}
.hero-copy h1{font-family:"Roboto Condensed",sans-serif;font-weight:400;font-size:40px;line-height:52px;letter-spacing:1px}
.hero-copy h1 b{font-weight:700}
.hero-copy p{font-family:"Montserrat",sans-serif;font-size:25px;margin-top:4px}
.hero-btn{display:inline-flex;align-items:center;margin-top:26px;height:38px;padding:0 26px 0 46px;border-radius:19px;background:rgba(255,255,255,.35);font-family:"Montserrat",sans-serif;font-size:13px;font-weight:700;letter-spacing:1px;position:relative}
.hero-btn::before{content:"";position:absolute;left:6px;top:6px;width:26px;height:26px;border-radius:50%;background:rgba(0,0,0,.35)}
.hero-dots{position:absolute;left:568px;top:510px;display:flex;gap:6px}
.hero-dots i{width:18px;height:4px;background:#fff;opacity:.6}
.hero-dots i.on{background:var(--red);opacity:1}

/* about */
.about{position:absolute;top:650px;left:0;width:1200px;height:455px;text-align:center}
.about .section-title{margin-top:62px}
.about .section-title small{font-size:20px;color:#555;font-weight:400}
.about-lead{width:910px;margin:28px auto 0;font-size:11.5px;line-height:21px;color:var(--text)}
.about-cols{display:flex;justify-content:space-between;width:910px;margin:28px auto 0;text-align:left}
.about-col{width:400px;display:flex;gap:14px}
.about-col svg{flex:none}
.about-col h3{font-family:"Montserrat",sans-serif;font-size:17px;font-weight:500;color:#333;margin-top:6px}
.about-col p{font-size:11.5px;line-height:19px;margin-top:6px}
.btn-red{display:inline-block;margin-top:26px;height:36px;line-height:36px;padding:0 22px 0 42px;border-radius:18px;background:var(--red);color:#fff;font-family:"Montserrat",sans-serif;font-size:12px;font-weight:700;position:relative}
.btn-red::before{content:"";position:absolute;left:8px;top:7px;width:22px;height:22px;border-radius:50%;background:rgba(255,255,255,.35)}

/* services */
.services{position:absolute;top:1105px;left:0;width:1200px;height:520px;background:var(--grey-bg)}
.services .section-title{margin-top:62px}
.service-grid{display:flex;gap:27px;position:absolute;top:140px;left:143px}
.service-card{width:208px;height:290px;background:#fff;border-radius:4px;box-shadow:0 2px 6px rgba(0,0,0,.12);text-align:center;position:relative}
.service-img{height:140px;border-radius:4px 4px 0 0;border-bottom:4px solid var(--red)}
.svc-icon{position:absolute;left:88px;top:120px;width:32px;height:32px;border-radius:50%;background:#fff;border:2px solid #ddd}
.service-card h3{font-family:"Montserrat",sans-serif;font-size:13.5px;font-weight:700;color:#222;margin-top:20px;line-height:18px}
.service-card p{font-size:11px;line-height:17px;margin:8px 16px 0;color:var(--muted)}
.plus{position:absolute;left:94px;bottom:-10px;width:20px;height:20px;border-radius:50%;background:#666;color:#fff;font-size:16px;line-height:19px;font-weight:700}
.plus.on{background:var(--red)}

/* audiences */
.audiences{position:absolute;top:1625px;left:0;width:1200px;height:478px;text-align:center}
.audiences .section-title{margin-top:62px}
.audiences .lead{font-size:11.5px;margin-top:22px}
.aud-row{position:absolute;top:185px;left:140px;display:flex;gap:42px}
.aud{width:152px}
.aud-circle{width:152px;height:152px;border-radius:50%;background:#fff;border:3px solid #eee;box-shadow:0 2px 8px rgba(0,0,0,.08);display:flex;align-items:center;justify-content:center}
.aud.on .aud-circle{border-color:var(--red)}
.aud h4{font-family:"Montserrat",sans-serif;font-size:15px;font-weight:500;color:#333;margin-top:30px;line-height:21px}
.aud.on h4{color:var(--red);font-weight:700}
.arrow-btn{position:absolute;top:250px;width:34px;height:34px;border-radius:50%;background:#fff;border:1px solid #ddd;box-shadow:0 1px 4px rgba(0,0,0,.12);display:flex;align-items:center;justify-content:center}

/* team */
.team{position:absolute;top:2103px;left:0;width:1200px;height:492px;background:var(--grey-bg);text-align:center}
.team .section-title{margin-top:62px}
.team-row{position:absolute;top:140px;left:155px;display:flex;gap:60px}
.member{width:178px}
.member-photo{width:178px;height:178px;border:3px solid #fff;box-shadow:0 1px 4px rgba(0,0,0,.15);background:linear-gradient(180deg,#e9e9e9,#bdbdbd)}
.member.on .member-photo{border-color:var(--red)}
.member h4{font-family:"Montserrat",sans-serif;font-size:14px;font-weight:600;letter-spacing:2px;color:#555;margin-top:26px}
.member span{display:block;font-size:11px;color:var(--muted);margin-top:6px}
.socials{display:flex;justify-content:center;gap:8px;margin-top:16px}
.socials i{width:26px;height:26px;border-radius:50%;background:#c9c9c9}
.member.on .socials i{background:var(--red)}
.member.on .socials i:nth-child(2){background:#2a9fd8}
.member.on .socials i:nth-child(3){background:#1a6fae}
.member.on .socials i:nth-child(1){background:#1d4f9c}
.team-arrow{position:absolute;top:250px}

/* blog */
.blog{position:absolute;top:2595px;left:0;width:1200px;height:600px}
.blog .section-title{margin-top:62px}
.post-row{position:absolute;top:140px;left:142px;display:flex;gap:21px}
.post{width:292px}
.post-img{height:215px;position:relative}
.post-date{position:absolute;left:0;top:0;width:36px;height:44px;background:var(--red);color:#fff;text-align:center;font-family:"Montserrat",sans-serif;font-size:11px;line-height:14px;padding-top:5px}
.post-date b{display:block;font-size:18px;line-height:22px}
.post h3{font-family:"Montserrat",sans-serif;font-size:13.5px;line-height:20px;color:var(--red);font-weight:700;margin-top:22px}
.post p{font-size:11.5px;line-height:19px;margin-top:14px}
.read-more{display:inline-block;margin-top:16px;font-family:"Montserrat",sans-serif;font-size:12px;font-weight:700;color:var(--red)}
.read-more::after{content:" \2192";color:#666;font-size:16px}

/* footer */
.site-footer{position:absolute;top:3195px;left:0;width:1200px;height:325px;background:linear-gradient(180deg,#e2151b,#c80f15);color:#fff}
.foot-col{position:absolute;top:62px}
.foot-col h5{font-family:"Montserrat",sans-serif;font-size:15px;font-weight:700;letter-spacing:1px}
.quick-links{left:142px}
.quick-links li{list-style:none;font-size:12px;margin-top:11px}
.quick-links li::before{content:"\203A";margin-right:14px}
.inquiry{left:338px;width:402px}
.inquiry-grid{display:grid;grid-template-columns:1fr 1fr;gap:8px;margin-top:18px}
.field{height:30px;background:#fff;color:#999;font-size:11px;padding:7px 8px}
.field.msg{grid-column:1/3;height:52px}
.submit{display:inline-block;margin-top:10px;width:120px;height:28px;line-height:28px;text-align:center;background:#ddd;color:#555;font-family:"Montserrat",sans-serif;font-weight:700;font-size:13px}
.contact{left:822px;width:240px}
.contact li{list-style:none;display:flex;gap:14px;font-size:11.5px;line-height:16px;margin-top:16px}
.contact li svg{flex:none}
.foot-socials{display:flex;gap:10px;margin-top:22px}
.foot-socials i{width:28px;height:28px;border-radius:50%;border:1.5px solid #fff}
.copyright{position:absolute;top:3520px;left:0;width:1200px;height:37px;background:#a80a0f;color:#fff;font-size:11px;line-height:37px;padding-left:142px}
.chat-bubble{position:absolute;left:1016px;top:3500px;width:42px;height:42px;border-radius:50%;background:var(--red);box-shadow:0 2px 6px rgba(0,0,0,.3);display:flex;align-items:center;justify-content:center}
</style>
</head>
<body>

<header class="site-header">
  <div class="brand"><span class="brand-mark"></span>Vaultmerrow</div>
  <nav class="main-nav">
    <a class="active">HOME</a><a>ABOUT</a><a>SERVICES</a><a>RESOURCES</a><a>BLOG</a><a>CONTACT US</a>
  </nav>
</header>

<section class="hero">
  <div class="hero-photo" role="img" aria-label="Hands holding a glowing red globe made of data and security icons"></div>
  <div class="hero-copy">
    <h1>DELIVERING <b>QUALITY</b><br>SERVICES THROUGH<br><b>INNOVATION</b></h1>
    <p>From Industry &nbsp;Experts</p>
    <a class="hero-btn">CONTACT US TODAY</a>
  </div>
  <svg class="hero-curve" viewBox="0 0 1200 120" preserveAspectRatio="none"><path d="M0 0 Q600 190 1200 0 L1200 120 L0 120Z" fill="#fff"/></svg>
  <div class="hero-dots"><i></i><i class="on"></i><i></i></div>
</section>

<section class="about">
  <h2 class="section-title"><b>About</b> <small>VAULTMERROW</small></h2>
  <div class="title-rule"></div>
  <p class="about-lead">Lorem ipsum dolor sit amet, consectetuer adipiscing elit, sed diam nonummy nibh euismod tincidunt ut laoreet dolore magna aliquam erat volutpat. Ut wisi enim ad minim veniam, quis nostrud exerci tation ullamcorper suscipit lobortis nisl ut aliquip ex ea commodo consequat. Duis autem vel eum iriure dolor in hendrerit in vulputate velit esse molestie consequat, vel illum dolore eu feugiat nulla facilisis at vero eros et accumsan et iusto odio dignissim qui blandit praesent luptatum zzril delenit augue duis dolore te feugait nulla facilisi nonummy nibh euismod tincidunt ut laoreet dolore magna aliquam.</p>
  <div class="about-cols">
    <div class="about-col">
      <svg width="52" height="52" viewBox="0 0 52 52" fill="none" stroke="#e3151c" stroke-width="2.5"><circle cx="24" cy="28" r="20"/><circle cx="24" cy="28" r="12"/><circle cx="24" cy="28" r="4" fill="#e3151c"/><path d="M24 28 L44 8 M38 8h6v6"/></svg>
      <div><h3>Our Mission</h3><p>Lamcorper suscipit lobortis nisl ut aliquip ex ea commodo consequat. Duis autem vel eum iriure dolor in hendrerit in vulputate velit esse molestie consequat, vel</p></div>
    </div>
    <div class="about-col">
      <svg width="52" height="52" viewBox="0 0 52 52" fill="none" stroke="#e3151c" stroke-width="2.5"><path d="M3 26 Q26 2 49 26 Q26 50 3 26Z"/><circle cx="26" cy="26" r="9"/><circle cx="26" cy="26" r="3.5" fill="#e3151c"/></svg>
      <div><h3>Our Vision</h3><p>Lamcorper suscipit lobortis nisl ut aliquip ex ea commodo consequat. Duis autem vel eum iriure dolor in hendrerit in vulputate velit esse molestie consequat, vel</p></div>
    </div>
  </div>
  <a class="btn-red">Read More</a>
</section>

<section class="services">
  <h2 class="section-title"><b>OUR</b> SERVICES</h2>
  <div class="title-rule"></div>
  <div class="service-grid">
    <article class="service-card">
      <div class="service-img" role="img" aria-label="Blue cloud computing and data network imagery" style="background:linear-gradient(135deg,#0a3b78,#2f8fd6)"></div>
      <span class="svc-icon"></span>
      <h3>Data Management<br>Services</h3>
      <p>Lorem ipsum dolor sit amet consectetuer adipiscing elit, sed diam nonummy nibh eui.</p>
      <span class="plus on">+</span>
    </article>
    <article class="service-card">
      <div class="service-img" role="img" aria-label="Hand touching a digital analytics interface" style="background:linear-gradient(135deg,#1b3f7a,#6e9fd0)"></div>
      <span class="svc-icon"></span>
      <h3>Data Management<br>Platforms</h3>
      <p>Lorem ipsum dolor sit amet consectetuer adipiscing elit, sed diam nonummy nibh eui.</p>
      <span class="plus">+</span>
    </article>
    <article class="service-card">
      <div class="service-img" role="img" aria-label="Engineer in safety vest at an industrial site" style="background:linear-gradient(135deg,#3a4b3e,#9aa07a)"></div>
      <span class="svc-icon"></span>
      <h3>Industry<br>Solutions</h3>
      <p>Lorem ipsum dolor sit amet consectetuer adipiscing elit, sed diam nonummy nibh eui.</p>
      <span class="plus">+</span>
    </article>
    <article class="service-card">
      <div class="service-img" role="img" aria-label="Digital padlock over a red and blue circuit background" style="background:linear-gradient(135deg,#0d2a5e,#8a1a3a)"></div>
      <span class="svc-icon"></span>
      <h3>Ransomware<br>Protection</h3>
      <p>Lorem ipsum dolor sit amet consectetuer adipiscing elit, sed diam nonummy nibh eui.</p>
      <span class="plus">+</span>
    </article>
  </div>
</section>

<section class="audiences">
  <h2 class="section-title"><b>TO WHOM</b> WE SERVE</h2>
  <div class="title-rule"></div>
  <p class="lead">Lorem ipsum dolor sit amet, consectetuer adipiscing elit, sed diam nonummy nibh euismod tincidunt ut laoreet dolore magna aliquam erat</p>
  <span class="arrow-btn" style="left:76px"><svg width="10" height="12" viewBox="0 0 10 12"><path d="M7 1 2 6l5 5" stroke="#666" stroke-width="2" fill="none"/></svg></span>
  <span class="arrow-btn" style="left:1090px"><svg width="10" height="12" viewBox="0 0 10 12"><path d="M3 1l5 5-5 5" stroke="#666" stroke-width="2" fill="none"/></svg></span>
  <div class="aud-row">
    <div class="aud"><div class="aud-circle"><svg width="60" height="60" viewBox="0 0 60 60" fill="none" stroke="#888" stroke-width="2"><path d="M26 6 3 48h46z"/><path d="M26 20v14M26 39v3"/><circle cx="44" cy="40" r="9" fill="#fff"/><circle cx="44" cy="37" r="3"/></svg></div><h4>Risk Managers</h4></div>
    <div class="aud"><div class="aud-circle"><svg width="60" height="60" viewBox="0 0 60 60" fill="none" stroke="#888" stroke-width="2"><path d="M30 5 9 13v16c0 14 10 22 21 26 11-4 21-12 21-26V13z"/><path d="M20 30l7 7 13-14"/></svg></div><h4>Information<br>Security</h4></div>
    <div class="aud on"><div class="aud-circle"><svg width="64" height="64" viewBox="0 0 64 64" fill="none" stroke="#e3151c" stroke-width="2"><rect x="14" y="14" width="36" height="36" rx="2"/><path d="M22 14V6M32 14V6M42 14V6M22 50v8M32 50v8M42 50v8M14 22H6M14 32H6M14 42H6M50 22h8M50 32h8M50 42h8"/><rect x="24" y="30" width="16" height="12"/><path d="M27 30v-4a5 5 0 0 1 10 0v4"/></svg></div><h4>Cyber Security<br>Professionals</h4></div>
    <div class="aud"><div class="aud-circle"><svg width="60" height="60" viewBox="0 0 60 60" fill="none" stroke="#888" stroke-width="2"><circle cx="30" cy="18" r="7"/><path d="M18 40c0-8 5-13 12-13s12 5 12 13"/><path d="M10 40h40v4H10zM16 44v10M44 44v10"/></svg></div><h4>Chief Data<br>Technicians</h4></div>
    <div class="aud"><div class="aud-circle"><svg width="60" height="60" viewBox="0 0 60 60" fill="none" stroke="#888" stroke-width="2"><path d="M20 18h20l-2-8H22z"/><circle cx="30" cy="25" r="7"/><path d="M14 54V44c0-6 7-10 16-10s16 4 16 10v10z"/><path d="M30 34v20"/></svg></div><h4>Digital<br>Officers</h4></div>
  </div>
</section>

<section class="team">
  <h2 class="section-title"><b>OUR</b> TEAM</h2>
  <div class="title-rule"></div>
  <svg class="team-arrow" style="left:62px" width="30" height="70" viewBox="0 0 30 70"><path d="M28 2 3 35l25 33" stroke="#ccc" stroke-width="2" fill="none"/></svg>
  <svg class="team-arrow" style="left:1106px" width="30" height="70" viewBox="0 0 30 70"><path d="M2 2l25 33L2 68" stroke="#ccc" stroke-width="2" fill="none"/></svg>
  <div class="team-row">
    <div class="member on"><div class="member-photo" role="img" aria-label="Portrait of a team member in a dark suit"></div><h4>CORIN TALLOW</h4><span>Designation</span><div class="socials"><i></i><i></i><i></i><i></i></div></div>
    <div class="member"><div class="member-photo" role="img" aria-label="Portrait of a team member in a black blazer"></div><h4>PRIYA OKONDE</h4><span>Designation</span><div class="socials"><i></i><i></i><i></i><i></i></div></div>
    <div class="member"><div class="member-photo" role="img" aria-label="Portrait of a team member in a grey suit"></div><h4>CORIN TALLOW</h4><span>Designation</span><div class="socials"><i></i><i></i><i></i><i></i></div></div>
    <div class="member"><div class="member-photo" role="img" aria-label="Portrait of a senior team member with glasses"></div><h4>TEODOR BRANDT</h4><span>Designation</span><div class="socials"><i></i><i></i><i></i><i></i></div></div>
  </div>
</section>

<section class="blog">
  <h2 class="section-title"><b>LATEST BLOG</b> POSTS</h2>
  <div class="title-rule"></div>
  <div class="post-row">
    <article class="post">
      <div class="post-img" role="img" aria-label="Group of business people standing together" style="background:linear-gradient(135deg,#d9dde3,#7e8794)"><span class="post-date">FEB<b>07</b></span></div>
      <h3>Lorem ipsum dolor sit amet, consectetuer adipiscing elit, sed diam nonummy</h3>
      <p>olore magna aliquam erat volutpat. Ut wisi enim minim veniam, quis nostrud exerci tationcorper suscipit lobortis nisl ut aliquip ex ea</p>
      <a class="read-more">Read More</a>
    </article>
    <article class="post">
      <div class="post-img" role="img" aria-label="Team working together over papers on a table" style="background:linear-gradient(135deg,#c9d6e2,#7f98b0)"><span class="post-date">FEB<b>07</b></span></div>
      <h3>Lorem ipsum dolor sit amet, consectetuer adipiscing elit, sed diam nonummy</h3>
      <p>olore magna aliquam erat volutpat. Ut wisi enim minim veniam, quis nostrud exerci tationcorper suscipit lobortis nisl ut aliquip ex ea</p>
      <a class="read-more">Read More</a>
    </article>
    <article class="post">
      <div class="post-img" role="img" aria-label="Bright modern office with people at desks" style="background:linear-gradient(135deg,#e4e0da,#9c8f82)"><span class="post-date">FEB<b>07</b></span></div>
      <h3>Lorem ipsum dolor sit amet, consectetuer adipiscing elit, sed diam nonummy</h3>
      <p>olore magna aliquam erat volutpat. Ut wisi enim minim veniam, quis nostrud exerci tationcorper suscipit lobortis nisl ut aliquip ex ea</p>
      <a class="read-more">Read More</a>
    </article>
  </div>
</section>

<footer class="site-footer">
  <div class="foot-col quick-links">
    <h5>QUICK LINKS</h5>
    <ul style="margin-top:10px"><li>Home</li><li>About</li><li>Services</li><li>Resources</li><li>Blog</li><li>Contact Us</li></ul>
  </div>
  <div class="foot-col inquiry">
    <h5>QUICK INQUIRY</h5>
    <div class="inquiry-grid">
      <div class="field">First Name</div><div class="field">Last Name</div>
      <div class="field">Phone</div><div class="field">Email</div>
      <div class="field msg">Message</div>
    </div>
    <span class="submit">SUBMIT</span>
  </div>
  <div class="foot-col contact">
    <h5>CONTACT DETAILS</h5>
    <ul>
      <li><svg width="14" height="18" viewBox="0 0 14 18"><path d="M7 0a7 7 0 0 0-7 7c0 5 7 11 7 11s7-6 7-11a7 7 0 0 0-7-7z" fill="#fff"/><circle cx="7" cy="7" r="2.5" fill="#d3121a"/></svg><span>Vaultmerrow<br>1234 Lorem Ipsum Dolor sit amet magna aliqua Sonnet CA 123</span></li>
      <li><svg width="14" height="14" viewBox="0 0 14 14"><path d="M3 0l3 3-2 2a9 9 0 0 0 5 5l2-2 3 3-2 3C6 14 0 8 0 2z" fill="#fff"/></svg><span>123-555-0148</span></li>
      <li><svg width="14" height="11" viewBox="0 0 14 11"><rect width="14" height="11" fill="#fff"/><path d="M0 0l7 6 7-6" stroke="#d3121a" fill="none"/></svg><span>info@vaultmerrow.com.au</span></li>
    </ul>
    <div class="foot-socials"><i></i><i></i><i></i><i></i></div>
  </div>
</footer>
<div class="copyright">Copyright 2019 @ Vaultmerrow. All Rights Reserved. &nbsp;|&nbsp; Terms of services / Privacy Policy</div>
<div class="chat-bubble"><svg width="22" height="18" viewBox="0 0 22 18"><path d="M2 1h18v11H8l-5 4v-4H2z" fill="#fff"/></svg></div>

</body>
</html>
```